New web design for a service provider in the medical field

We are looking for a new design for our website. We are a company that repairs and sells medical endoscopes. Our customers include doctors and hospitals. Our current website can be found at https://lumavex.de/en/lumavex-english.
We need a new web design (without programming) for the following 3 pages:
-Startpage https://lumavex.de/en/lumavex-english/
-Used endoscopes https://lumavex.de/en/used-endoscopes/
-Purchase https://lumavex.de/en/purchase/
The design should be modern and stylish.
The blue color of the logo should be reflected on the page, but not too intrusive.
I have uploaded the images from the header. If more images are needed, let me know and I will upload them.

Target Market(s)
Doctors and hospitals

```html
<!DOCTYPE html>
<html lang="en">
<head>
<meta charset="utf-8">
<title>Lumavex – Homepage Concepts</title>
<link href="https://fonts.googleapis.com/css2?family=Exo+2:wght@500;600&family=Open+Sans:wght@400;600&display=swap" rel="stylesheet">
<style>
:root{
  --blue:#0a4aa6;
  --sky:#2a9fdf;
  --ink:#1f2329;
  --text:#555b63;
  --muted:#8a9099;
  --soft:#f4f5f7;
  --line:#e1e4e8;
  --dark:#1d2025;
  --board:#e4e7ea;
  --white:#ffffff;
}
*{box-sizing:border-box;margin:0;padding:0}
html,body{width:840px;height:1200px;overflow:hidden;background:var(--board)}
body{font-family:"Open Sans",Arial,sans-serif;color:var(--text)}
.board{width:1607px;height:2296px;transform:scale(0.52271);transform-origin:0 0;position:relative;
  background:radial-gradient(circle at 50% 40%,#eef0f2,var(--board))}
.page{position:absolute;top:69px;width:534px;height:2158px;background:var(--white);overflow:hidden;box-shadow:0 6px 24px rgba(0,0,0,.12)}
.page--a{left:183px}
.page--b{left:891px}
.abs{position:absolute}
h1,h2,h3,.heading{font-family:"Exo 2",Arial,sans-serif;font-weight:600;color:var(--ink)}
.kicker{font-size:9.5px;color:var(--blue);font-weight:600}
.center{left:0;right:0;text-align:center}
.btn{position:absolute;display:flex;align-items:center;justify-content:center;border-radius:14px;background:var(--sky);color:var(--white);font-size:8px;font-weight:600;text-transform:uppercase}
.btn--white{background:var(--white);color:var(--blue)}

/* header */
.brand{position:absolute;left:48px;top:22px;display:flex;align-items:center;gap:5px;font-family:"Open Sans",Arial,sans-serif;font-weight:600;font-size:12.5px;color:var(--blue)}
.brand i{width:9px;height:9px;border-radius:50%;background:var(--sky);display:block}
.toplinks{position:absolute;left:185px;top:14px;font-size:6.5px;color:var(--muted)}
.toplinks b{font-weight:400;color:var(--blue)}
.nav{position:absolute;left:142px;top:36px;display:flex;gap:8px;font-size:7px;color:var(--ink);font-weight:600}
.page--b .toplinks{top:18px}
.page--b .nav{top:44px}
.page--b .brand{top:24px}

/* hero */
.hero-a-title{top:84px;font-size:24px}
.hero-b-title{left:50px;top:118px;font-size:23px;color:var(--white);line-height:1.35}
.hero-b-copy{left:50px;top:190px;width:215px;font-size:6.6px;line-height:1.75;color:#e8ebef}

/* intro */
.intro-kicker{left:297px;top:372px;width:200px;line-height:1.4}
.intro-title{left:297px;top:403px;font-size:17.5px;line-height:1.25}
.intro-copy{left:297px;top:457px;width:190px;font-size:6.5px;line-height:1.8}

/* services */
.services{top:583px;height:266px;left:0;right:0;background:var(--soft)}
.section-kicker{font-size:9.5px;color:var(--blue);font-weight:600}
.section-title{font-size:16px}
.card{position:absolute;top:84px;width:136px;height:149px;background:var(--white);text-align:center;box-shadow:0 2px 8px rgba(0,0,0,.04)}
.card svg{margin-top:6px}
.card h3{font-family:"Open Sans",Arial,sans-serif;font-size:7.6px;font-weight:600;margin-top:8px}
.card p{font-size:6.2px;line-height:1.55;color:var(--muted);margin:6px 10px 0}
.card .btn{left:30px;top:114px;width:77px;height:24px;font-size:6.5px}
.card--featured{background:var(--blue)}
.card--featured h3,.card--featured p{color:var(--white)}

/* faulty */
.faulty-photo{left:234px;top:849px;width:300px;height:216px}
.faulty-card{left:46px;top:879px;width:203px;height:159px;background:var(--white);box-shadow:0 4px 16px rgba(0,0,0,.08)}
.faulty-card h2{position:absolute;left:16px;top:30px;font-size:16.5px}
.faulty-card .lead{position:absolute;left:16px;top:58px;font-size:7px;color:var(--muted)}
.faulty-card .note{position:absolute;left:16px;top:80px;font-size:7px;color:var(--ink)}

/* products */
.tab{position:absolute;left:50px;width:103px;height:33px;border:1px solid var(--line);display:flex;align-items:center;justify-content:center;font-size:8px;color:var(--ink)}
.tab--active{background:var(--blue);color:var(--white);border-color:var(--blue);width:114px;clip-path:polygon(0 0,103px 0,114px 50%,103px 100%,0 100%)}
.product-title{left:334px;top:1156px;width:170px;font-size:8.5px;line-height:1.55;color:var(--ink)}
.product-copy{left:334px;top:1188px;width:140px;font-size:6.3px;line-height:1.75;color:var(--muted)}

/* decision */
.decision{left:0;top:1309px;width:534px;height:278px}
.dec-kicker{left:297px;top:1331px;color:var(--sky)}
.dec-title{left:297px;top:1346px;font-size:17px;color:var(--white);line-height:1.2}
.acc{position:absolute;left:297px;width:187px;height:19px;border:1px solid rgba(255,255,255,.55);font-size:7px;color:var(--white);display:flex;align-items:center;justify-content:space-between;padding:0 7px}
.acc--open{background:var(--white);color:var(--ink)}
.acc-note{left:304px;top:1425px;font-size:6.3px;color:#e9ecef}

/* benefits */
.benefit{position:absolute;top:1668px;width:74px;text-align:center;font-size:8px;line-height:1.45;color:var(--ink)}
.benefit .ring{width:62px;height:62px;border:1.5px solid #c9d4e6;border-radius:50%;margin:0 auto 8px;display:flex;align-items:center;justify-content:center;background:var(--white)}

/* contact */
.contact{top:1797px;left:0;right:0;height:240px;background:var(--soft)}
.contact-item{position:absolute;top:1878px;text-align:center;font-size:7px;color:var(--ink)}
.contact-item .dot{width:14px;height:14px;border:1px solid var(--sky);border-radius:50%;margin:0 auto 5px;display:flex;align-items:center;justify-content:center}

/* footer */
.footer-wave{left:0;top:1905px;width:534px;height:253px}
.foot-brand{left:48px;top:2027px;display:flex;align-items:center;gap:6px;font-weight:600;font-size:19px;color:var(--white)}
.foot-brand i{width:12px;height:12px;border-radius:50%;background:var(--white);display:block}
.foot-col{position:absolute;top:1999px;font-size:6.6px;line-height:1.8;color:#c7cbd1}
.foot-col h4{font-size:8px;font-weight:600;color:var(--white);margin-bottom:5px}
.foot-rule{left:48px;right:48px;top:2113px;height:1px;background:#3a3e45}
.copyright{left:48px;top:2131px;font-size:6.6px;color:#c7cbd1}
.social{position:absolute;top:2126px;width:17px;height:17px;border:1px solid var(--sky);border-radius:50%}
</style>
</head>
<body>
<div class="board">

<!-- ============ Concept A ============ -->
<section class="page page--a">
  <svg class="abs" style="left:0;top:0" width="534" height="380" viewBox="0 0 534 380" role="img" aria-label="Product photo of endoscope control handles on a light background">
    <rect width="534" height="380" fill="#eef0f2"/>
    <rect y="150" width="534" height="230" fill="url(#ga)"/>
    <defs><linearGradient id="ga" x1="0" y1="0" x2="1" y2="1"><stop offset="0" stop-color="#e6e8ea"/><stop offset=".5" stop-color="#b9bec4"/><stop offset="1" stop-color="#dde0e3"/></linearGradient></defs>
    <path d="M0 380 L0 345 C110 392 210 372 310 320 C390 280 470 300 534 360 L534 380 Z" fill="#fff"/>
  </svg>
  <div class="brand"><i></i>Lumavex</div>
  <div class="toplinks">Home | About us | Contact Us &nbsp;&nbsp; <b>✉</b> info@lumavex.de | <b>✆</b> +49 4000 555 120-0 &nbsp;&nbsp; En ˅</div>
  <nav class="nav"><span>Endoscope Repair</span><span>Used Endoscopes</span><span>Endoscopy Systems</span><span>Endoscopy Accessories</span><span>Purchase</span></nav>
  <h1 class="abs center hero-a-title">YOUR FUTURE - OUR SERVICE</h1>
  <div class="btn" style="left:218px;top:131px;width:98px;height:28px">Pick-up order</div>

  <div class="abs" style="left:0;top:390px;width:250px;height:193px;background:linear-gradient(135deg,#d9dcdf,#8d939a 60%,#c7cbcf)" role="img" aria-label="Photo of an endoscope control body on a stand"></div>
  <p class="abs kicker intro-kicker">Endoscope repairs and second hand endoscopes from Lumavex –</p>
  <h2 class="abs intro-title">CAUSE THE OUTCOME<br>MATTERS!</h2>
  <p class="abs intro-copy">Lumavex is a privileged partner for the start-up facility or optimisation of existing healthcare facilities, doctor's offices and hospitals. The quality and reliability of our products and our offered service are our best advertisement!</p>
  <div class="btn" style="left:297px;top:525px;width:65px;height:25px">Read more</div>

  <div class="abs services">
    <p class="abs center section-kicker" style="top:24px">Services</p>
    <h2 class="abs center section-title" style="top:44px">WHAT WE DO</h2>
    <div class="card" style="left:50px"><svg width="38" height="38" viewBox="0 0 38 38" fill="none" stroke="#0a4aa6" stroke-width="1.5"><path d="M6 32 L30 8 M8 8 L32 32"/><circle cx="30" cy="8" r="4"/><circle cx="8" cy="8" r="4"/></svg><h3>Endoscope Repair Service</h3><p>Manufacturer-independent we repair and maintain endoscopes, individual components</p><div class="btn">Repair request</div></div>
    <div class="card card--featured" style="left:199px"><svg width="38" height="38" viewBox="0 0 38 38" fill="none" stroke="#fff" stroke-width="1.5"><path d="M19 5 L9 16 M19 5 L29 16"/><circle cx="19" cy="5" r="2"/><rect x="4" y="16" width="30" height="15" rx="2"/><text x="19" y="27" font-size="8" fill="#fff" stroke="none" text-anchor="middle" font-family="Open Sans" font-weight="600">SALE</text></svg><h3>Sale Used endoscopes</h3><p>Manufacturer-independent we repair and maintain endoscopes, individual components</p><div class="btn btn--white">Repair request</div></div>
    <div class="card" style="left:348px"><svg width="38" height="38" viewBox="0 0 38 38" fill="none" stroke="#0a4aa6" stroke-width="1.5"><rect x="16" y="3" width="16" height="24" rx="2"/><circle cx="24" cy="13" r="3"/><path d="M18 20 L10 28 L8 36 M14 22 L19 27"/></svg><h3>Purchase Used endoscopes</h3><p>Manufacturer-independent we repair and maintain endoscopes, individual components</p><div class="btn">Repair request</div></div>
  </div>

  <div class="abs faulty-photo" style="background:linear-gradient(120deg,#eceef0,#b3b8be 55%,#e2e4e6)" role="img" aria-label="Photo of white endoscope holders on a stand"></div>
  <div class="abs faulty-card"><h2>FAULTY ENDOSCOPE?</h2><p class="lead">We ensure quick and smooth repairs!</p><p class="note">Simple place a</p><div class="btn" style="left:16px;top:99px;width:98px;height:28px">Pick-up order</div></div>

  <p class="abs center section-kicker" style="top:1096px">Products</p>
  <h2 class="abs center section-title" style="top:1116px">USED ENDOSCOPES</h2>
  <div class="tab tab--active" style="top:1153px">ORVANA</div>
  <div class="tab" style="top:1191px">PENTRIX</div>
  <div class="tab" style="top:1229px">FUJARA</div>
  <div class="abs" style="left:176px;top:1153px;width:142px;height:111px;background:linear-gradient(135deg,#c9cdd1,#6d737a 55%,#b7bcc1)" role="img" aria-label="Photo of second hand endoscopes"></div>
  <p class="abs product-title">Second hand Orvana-endoscopes and -processors</p>
  <p class="abs product-copy">Lumavex GmbH offers you excellent second hand Orvana equipment (endoscopes and processors) as a cost-effective and high-quality alternative to buying new devices.</p>
  <div class="btn" style="left:334px;top:1252px;width:65px;height:24px">Read more</div>

  <div class="abs decision" style="background:linear-gradient(90deg,#d4d6d8,#9ea2a6 45%,#6e7378)" role="img" aria-label="Photo of a technician in gloves repairing an endoscope"></div>
  <p class="abs kicker dec-kicker">Lumavex GmbH,</p>
  <h2 class="abs dec-title">YOUR DECISION FOR<br>YOUR FUTURE</h2>
  <div class="acc acc--open" style="top:1402px">One company for everyone<span>˅</span></div>
  <p class="abs acc-note">We are a service provider for doctors and hospitals!</p>
  <div class="acc" style="top:1443px">Experience characterises us<span>˄</span></div>
  <div class="acc" style="top:1468px">The product is close to our hearts<span>˄</span></div>
  <div class="acc" style="top:1493px">Guaranteed Service<span>˄</span></div>
  <div class="acc" style="top:1518px">Quality not quantity<span>˄</span></div>
  <div class="acc" style="top:1543px">Services for everyone<span>˄</span></div>

  <p class="abs center section-kicker" style="top:1618px">Benefits</p>
  <h2 class="abs center section-title" style="top:1638px">WHY CHOOSE US</h2>
  <div class="benefit" style="left:44px"><div class="ring"><svg width="28" height="28" viewBox="0 0 28 28" fill="none" stroke="#0a4aa6" stroke-width="1.4"><circle cx="16" cy="15" r="9"/><path d="M16 15 L16 9 M14 3 h4 M2 13 h6 M3 18 h5"/></svg></div>Fast<br>repairs</div>
  <div class="benefit" style="left:118px"><div class="ring"><svg width="28" height="28" viewBox="0 0 28 28" fill="none" stroke="#0a4aa6" stroke-width="1.4"><rect x="3" y="8" width="14" height="11"/><path d="M17 11 h5 l3 4 v4 h-8"/><circle cx="8" cy="21" r="2"/><circle cx="21" cy="21" r="2"/></svg></div>On-site<br>service</div>
  <div class="benefit" style="left:193px"><div class="ring"><svg width="28" height="28" viewBox="0 0 28 28" fill="none" stroke="#0a4aa6" stroke-width="1.4"><rect x="5" y="3" width="16" height="22"/><path d="M9 9 h8 M9 13 h8 M9 17 h5 M24 6 L15 19"/></svg></div>Without a<br>maintenance<br>contract</div>
  <div class="benefit" style="left:267px"><div class="ring"><svg width="28" height="28" viewBox="0 0 28 28" fill="none" stroke="#0a4aa6" stroke-width="1.4"><rect x="4" y="16" width="5" height="8"/><rect x="11" y="12" width="5" height="12"/><rect x="18" y="8" width="5" height="16"/><path d="M4 11 L12 5 L17 7 L24 2"/></svg></div>Highly cost<br>efficient</div>
  <div class="benefit" style="left:342px"><div class="ring"><svg width="28" height="28" viewBox="0 0 28 28" fill="none" stroke="#0a4aa6" stroke-width="1.4"><circle cx="14" cy="14" r="10" stroke-dasharray="4 2"/><circle cx="14" cy="14" r="6"/><circle cx="14" cy="12" r="2"/></svg></div>Loan equipment<br>service</div>
  <div class="benefit" style="left:416px"><div class="ring"><svg width="28" height="28" viewBox="0 0 28 28" fill="none" stroke="#0a4aa6" stroke-width="1.4"><circle cx="14" cy="14" r="11" stroke-dasharray="2 3"/><path d="M9 14 h3 v7 h-3z M12 15 l3 -5 v-2 h2 v5 h4 l-1 8 h-8"/></svg></div>First class<br>service</div>

  <div class="abs contact">
    <p class="abs center section-kicker" style="top:24px">Contact Us</p>
    <h2 class="abs center section-title" style="top:44px">HOW CAN WE HELP YOU?</h2>
  </div>
  <div class="contact-item" style="left:145px"><div class="dot"><svg width="7" height="7" viewBox="0 0 10 10"><path d="M2 1 L4 1 L5 3 L4 4 Q5 6 6 6 L7 5 L9 6 L9 8 Q3 9 2 1Z" fill="#2a9fdf"/></svg></div>Call Us +49 4000 555 120-0</div>
  <div class="contact-item" style="left:275px"><div class="dot"><svg width="7" height="6" viewBox="0 0 10 8"><rect width="10" height="8" fill="#2a9fdf"/><path d="M0 0 L5 4 L10 0" stroke="#fff" fill="none"/></svg></div>Email Us info@lumavex.de</div>

  <svg class="abs footer-wave" viewBox="0 0 534 253"><path d="M0 32 C60 5 120 10 200 40 C300 80 420 40 534 30 L534 253 L0 253 Z" fill="#1d2025"/></svg>
  <div class="abs foot-brand"><i></i>Lumavex</div>
  <div class="foot-col" style="left:249px"><h4>Quick Links</h4>Informations<br>About Us<br>Contact Us<br>Tos<br>Copyrights<br>Privacy Policy</div>
  <div class="foot-col" style="left:348px"><h4>Contact Address</h4><span style="color:#2a9fdf">●</span> Lindenweg 12<br>&nbsp;&nbsp;21000 Musterstadt<br>&nbsp;&nbsp;Germany<h4 style="margin-top:10px">Opening Hours</h4>Monday – Friday<br>08:00 – 20:00</div>
  <div class="abs foot-rule"></div>
  <p class="abs copyright">© 2022 Lumavex GmbH. All rights reserved.</p>
  <span class="social" style="left:442px"></span><span class="social" style="left:465px"></span>
</section>

<!-- ============ Concept B ============ -->
<section class="page page--b">
  <svg class="abs" style="left:0;top:62px" width="534" height="310" viewBox="0 0 534 310" role="img" aria-label="Photo of gloved hands holding an endoscope in a clinic">
    <defs><linearGradient id="gb" x1="0" y1="0" x2="1" y2="0"><stop offset="0" stop-color="#3f464e"/><stop offset=".55" stop-color="#6c737b"/><stop offset="1" stop-color="#c9cdd1"/></linearGradient></defs>
    <rect width="534" height="310" fill="url(#gb)"/>
    <path d="M0 310 L0 290 C80 320 200 300 300 260 C390 225 470 230 534 260 L534 310 Z" fill="#fff"/>
  </svg>
  <div class="brand"><i></i>Lumavex</div>
  <div class="toplinks">Home | About us | Contact Us &nbsp;&nbsp; <b>✉</b> info@lumavex.de | <b>✆</b> +49 4000 555 120-0 &nbsp;&nbsp; En ˅</div>
  <nav class="nav"><span>Endoscope Repair</span><span>Used Endoscopes</span><span>Endoscopy Systems</span><span>Endoscopy Accessories</span><span>Purchase</span></nav>
  <h1 class="abs hero-b-title">YOUR FUTURE -<br>OUR SERVICE</h1>
  <p class="abs hero-b-copy">Lumavex GmbH is specialised in the repair and sale of Orvana, Pentrix and Fujara flexible medical endoscopes. As a service-oriented company, we are at your side with our knowledge and skills!</p>
  <div class="btn" style="left:50px;top:250px;width:98px;height:27px">Pick-up order</div>

  <div class="abs" style="left:0;top:390px;width:250px;height:193px;background:linear-gradient(135deg,#d9dcdf,#8d939a 60%,#c7cbcf)" role="img" aria-label="Photo of an endoscope control body on a stand"></div>
  <p class="abs kicker intro-kicker">Endoscope repairs and second hand endoscopes from Lumavex –</p>
  <h2 class="abs intro-title">CAUSE THE OUTCOME<br>MATTERS!</h2>
  <p class="abs intro-copy">Lumavex is a privileged partner for the start-up facility or optimisation of existing healthcare facilities, doctor's offices and hospitals. The quality and reliability of our products and our offered service are our best advertisement!</p>
  <div class="btn" style="left:297px;top:525px;width:65px;height:25px">Read more</div>

  <div class="abs services">
    <p class="abs center section-kicker" style="top:24px">Services</p>
    <h2 class="abs center section-title" style="top:44px">WHAT WE DO</h2>
    <div class="card" style="left:50px"><svg width="38" height="38" viewBox="0 0 38 38" fill="none" stroke="#0a4aa6" stroke-width="1.5"><path d="M6 32 L30 8 M8 8 L32 32"/><circle cx="30" cy="8" r="4"/><circle cx="8" cy="8" r="4"/></svg><h3>Endoscope Repair Service</h3><p>Manufacturer-independent we repair and maintain endoscopes, individual components</p><div class="btn">Repair request</div></div>
    <div class="card card--featured" style="left:199px"><svg width="38" height="38" viewBox="0 0 38 38" fill="none" stroke="#fff" stroke-width="1.5"><path d="M19 5 L9 16 M19 5 L29 16"/><circle cx="19" cy="5" r="2"/><rect x="4" y="16" width="30" height="15" rx="2"/><text x="19" y="27" font-size="8" fill="#fff" stroke="none" text-anchor="middle" font-family="Open Sans" font-weight="600">SALE</text></svg><h3>Sale Used endoscopes</h3><p>Manufacturer-independent we repair and maintain endoscopes, individual components</p><div class="btn btn--white">Repair request</div></div>
    <div class="card" style="left:348px"><svg width="38" height="38" viewBox="0 0 38 38" fill="none" stroke="#0a4aa6" stroke-width="1.5"><rect x="16" y="3" width="16" height="24" rx="2"/><circle cx="24" cy="13" r="3"/><path d="M18 20 L10 28 L8 36 M14 22 L19 27"/></svg><h3>Purchase Used endoscopes</h3><p>Manufacturer-independent we repair and maintain endoscopes, individual components</p><div class="btn">Repair request</div></div>
  </div>

  <div class="abs faulty-photo" style="background:linear-gradient(120deg,#e8e9ee,#9ea2ab 55%,#cfd1d8)" role="img" aria-label="Photo of coiled endoscopes and parts on a table"></div>
  <div class="abs faulty-card"><h2>FAULTY ENDOSCOPE?</h2><p class="lead">We ensure quick and smooth repairs!</p><p class="note">Simple place a</p><div class="btn" style="left:16px;top:99px;width:98px;height:28px">Pick-up order</div></div>

  <p class="abs center section-kicker" style="top:1096px">Products</p>
  <h2 class="abs center section-title" style="top:1116px">USED ENDOSCOPES</h2>
  <div class="tab tab--active" style="top:1153px">ORVANA</div>
  <div class="tab" style="top:1191px">PENTRIX</div>
  <div class="tab" style="top:1229px">FUJARA</div>
  <div class="abs" style="left:176px;top:1153px;width:142px;height:111px;background:linear-gradient(135deg,#c9cdd1,#6d737a 55%,#b7bcc1)" role="img" aria-label="Photo of second hand endoscopes"></div>
  <p class="abs product-title">Second hand Orvana-endoscopes and -processors</p>
  <p class="abs product-copy">Lumavex GmbH offers you excellent second hand Orvana equipment (endoscopes and processors) as a cost-effective and high-quality alternative to buying new devices.</p>
  <div class="btn" style="left:334px;top:1252px;width:65px;height:24px">Read more</div>

  <div class="abs decision" style="background:linear-gradient(90deg,#d4d6d8,#9ea2a6 45%,#6e7378)" role="img" aria-label="Photo of a technician in gloves repairing an endoscope"></div>
  <p class="abs kicker dec-kicker">Lumavex GmbH,</p>
  <h2 class="abs dec-title">YOUR DECISION FOR<br>YOUR FUTURE</h2>
  <div class="acc acc--open" style="top:1402px">One company for everyone<span>˅</span></div>
  <p class="abs acc-note">We are a service provider for doctors and hospitals!</p>
  <div class="acc" style="top:1443px">Experience characterises us<span>˄</span></div>
  <div class="acc" style="top:1468px">The product is close to our hearts<span>˄</span></div>
  <div class="acc" style="top:1493px">Guaranteed Service<span>˄</span></div>
  <div class="acc" style="top:1518px">Quality not quantity<span>˄</span></div>
  <div class="acc" style="top:1543px">Services for everyone<span>˄</span></div>

  <p class="abs center section-kicker" style="top:1618px">Benefits</p>
  <h2 class="abs center section-title" style="top:1638px">WHY CHOOSE US</h2>
  <div class="benefit" style="left:44px"><div class="ring"><svg width="28" height="28" viewBox="0 0 28 28" fill="none" stroke="#0a4aa6" stroke-width="1.4"><circle cx="16" cy="15" r="9"/><path d="M16 15 L16 9 M14 3 h4 M2 13 h6 M3 18 h5"/></svg></div>Fast<br>repairs</div>
  <div class="benefit" style="left:118px"><div class="ring"><svg width="28" height="28" viewBox="0 0 28 28" fill="none" stroke="#0a4aa6" stroke-width="1.4"><rect x="3" y="8" width="14" height="11"/><path d="M17 11 h5 l3 4 v4 h-8"/><circle cx="8" cy="21" r="2"/><circle cx="21" cy="21" r="2"/></svg></div>On-site<br>service</div>
  <div class="benefit" style="left:193px"><div class="ring"><svg width="28" height="28" viewBox="0 0 28 28" fill="none" stroke="#0a4aa6" stroke-width="1.4"><rect x="5" y="3" width="16" height="22"/><path d="M9 9 h8 M9 13 h8 M9 17 h5 M24 6 L15 19"/></svg></div>Without a<br>maintenance<br>contract</div>
  <div class="benefit" style="left:267px"><div class="ring"><svg width="28" height="28" viewBox="0 0 28 28" fill="none" stroke="#0a4aa6" stroke-width="1.4"><rect x="4" y="16" width="5" height="8"/><rect x="11" y="12" width="5" height="12"/><rect x="18" y="8" width="5" height="16"/><path d="M4 11 L12 5 L17 7 L24 2"/></svg></div>Highly cost<br>efficient</div>
  <div class="benefit" style="left:342px"><div class="ring"><svg width="28" height="28" viewBox="0 0 28 28" fill="none" stroke="#0a4aa6" stroke-width="1.4"><circle cx="14" cy="14" r="10" stroke-dasharray="4 2"/><circle cx="14" cy="14" r="6"/><circle cx="14" cy="12" r="2"/></svg></div>Loan equipment<br>service</div>
  <div class="benefit" style="left:416px"><div class="ring"><svg width="28" height="28" viewBox="0 0 28 28" fill="none" stroke="#0a4aa6" stroke-width="1.4"><circle cx="14" cy="14" r="11" stroke-dasharray="2 3"/><path d="M9 14 h3 v7 h-3z M12 15 l3 -5 v-2 h2 v5 h4 l-1 8 h-8"/></svg></div>First class<br>service</div>

  <div class="abs contact">
    <p class="abs center section-kicker" style="top:24px">Contact Us</p>
    <h2 class="abs center section-title" style="top:44px">HOW CAN WE HELP YOU?</h2>
  </div>
  <div class="contact-item" style="left:145px"><div class="dot"><svg width="7" height="7" viewBox="0 0 10 10"><path d="M2 1 L4 1 L5 3 L4 4 Q5 6 6 6 L7 5 L9 6 L9 8 Q3 9 2 1Z" fill="#2a9fdf"/></svg></div>Call Us +49 4000 555 120-0</div>
  <div class="contact-item" style="left:275px"><div class="dot"><svg width="7" height="6" viewBox="0 0 10 8"><rect width="10" height="8" fill="#2a9fdf"/><path d="M0 0 L5 4 L10 0" stroke="#fff" fill="none"/></svg></div>Email Us info@lumavex.de</div>

  <svg class="abs footer-wave" viewBox="0 0 534 253"><path d="M0 32 C60 5 120 10 200 40 C300 80 420 40 534 30 L534 253 L0 253 Z" fill="#1d2025"/></svg>
  <div class="abs foot-brand"><i></i>Lumavex</div>
  <div class="foot-col" style="left:249px"><h4>Quick Links</h4>Informations<br>About Us<br>Contact Us<br>Tos<br>Copyrights<br>Privacy Policy</div>
  <div class="foot-col" style="left:348px"><h4>Contact Address</h4><span style="color:#2a9fdf">●</span> Lindenweg 12<br>&nbsp;&nbsp;21000 Musterstadt<br>&nbsp;&nbsp;Germany<h4 style="margin-top:10px">Opening Hours</h4>Monday – Friday<br>08:00 – 20:00</div>
  <div class="abs foot-rule"></div>
  <p class="abs copyright">© 2022 Lumavex GmbH. All rights reserved.</p>
  <span class="social" style="left:442px"></span><span class="social" style="left:465px"></span>
</section>

</div>
</body>
</html>
```